SkyvornQ Business Cards and Stationary Design

Need a design for our business cards and stationary. I want to carry on the theme of the logo. I want the business cards to have a design on the back. I would like the business cards and the stationary to carry the same theme, design scheme, and branding

Target Market(s)

Airlines and Maintenance Facilities

Industry/Entity Type

Aviation

Contact Information for Business Card

Name
Position Title
Address: 4827 Trellis Hollow Road, Fort Pierce, Florida, 34951
Office Number
Mobile Number
Email
Website

Font styles to use
Serif
Sans Serif

Colors

Designer to choose colors to be used in the design.

```html
<!DOCTYPE html>
<html lang="en">
<head>
<meta charset="utf-8">
<title>SkyvornQ Business Card</title>
<link href="https://fonts.googleapis.com/css2?family=Source+Sans+3:wght@400;600;700&display=swap" rel="stylesheet">
<style>
  :root {
    --backdrop: #dcdddf;
    --card: #ffffff;
    --navy: #14284f;
    --royal: #223a7a;
    --sky: #2a9ad8;
    --ink: #1d1d1f;
    --rule: #c9c9c9;
    --outline: #2a2a2a;
  }
  html, body {
    margin: 0;
    padding: 0;
    width: 1200px;
    height: 1103px;
    overflow: hidden;
    background: var(--backdrop);
    font-family: "Source Sans 3", Arial, sans-serif;
  }
  .canvas { position: relative; width: 1200px; height: 1103px; }
  .card {
    position: absolute;
    width: 789px;
    height: 450px;
    background: var(--card);
    border: 1px solid var(--outline);
    border-radius: 40px;
    overflow: hidden;
    box-sizing: border-box;
  }
  .card--front { left: 72px; top: 61px; }
  .card--back { left: 335px; top: 571px; }

  .brand { position: absolute; text-align: center; }
  .brand__ring {
    display: block;
    margin: 0 auto;
    border: 6px solid var(--royal);
    border-radius: 50%;
    box-sizing: border-box;
  }
  .brand__name {
    display: block;
    color: var(--navy);
    font-weight: 700;
    white-space: nowrap;
    line-height: 1;
  }
  .card--front .brand { left: 50px; top: 132px; width: 336px; }
  .card--front .brand__ring { width: 104px; height: 104px; }
  .card--front .brand__name { font-size: 42px; letter-spacing: 9px; margin-top: 18px; }

  .divider {
    position: absolute;
    left: 418px; top: 87px;
    width: 2px; height: 258px;
    background: var(--rule);
  }
  .details { position: absolute; left: 458px; top: 82px; color: var(--ink); }
  .details__name {
    margin: 0;
    font-size: 29px; font-weight: 700;
    color: var(--navy);
    letter-spacing: 0.5px;
    line-height: 1.1;
  }
  .details__title {
    margin: 4px 0 0;
    font-size: 25px; font-weight: 400;
    color: #333;
    line-height: 1.1;
  }
  .contact-list { list-style: none; margin: 20px 0 0; padding: 0; font-size: 19px; }
  .contact-list li { display: flex; align-items: center; height: 28px; }
  .contact-list svg { width: 17px; height: 17px; margin-right: 6px; flex: none; }
  .contact-list .address { align-items: flex-start; height: auto; margin-top: 13px; line-height: 28px; }
  .contact-list .address svg { margin-top: 5px; }

  .waves { position: absolute; left: 0; bottom: 0; width: 789px; height: 92px; }

  .card--back .brand { left: 0; width: 100%; top: 98px; }
  .card--back .brand__ring { width: 144px; height: 144px; border-width: 8px; }
  .card--back .brand__name { font-size: 50px; letter-spacing: 10px; margin-top: 24px; }
  .back__web {
    position: absolute; left: 0; width: 100%; top: 370px;
    margin: 0;
    text-align: center;
    font-size: 26px; letter-spacing: 5px; line-height: 30px;
    color: var(--ink);
  }
</style>
</head>
<body>
<div class="canvas">

  <section class="card card--front">
    <div class="brand">
      <span class="brand__ring"></span>
      <span class="brand__name">SKYVORNQ</span>
    </div>
    <div class="divider"></div>
    <div class="details">
      <h1 class="details__name">MARLOW QUENBY</h1>
      <p class="details__title">PRESIDENT</p>
      <ul class="contact-list">
        <li>
          <svg viewBox="0 0 20 20"><circle cx="10" cy="10" r="8.5" fill="none" stroke="var(--royal)" stroke-width="1.6"/><path d="M6.5 5.5c1 0 1.5 2 1 2.6l-.6.6c.6 1.4 1.6 2.4 3 3l.6-.6c.6-.5 2.6 0 2.6 1s-1 2-2 2c-3 0-6.4-3.4-6.4-6.4 0-1 .8-2.2 1.8-2.2z" fill="var(--royal)"/></svg>
          772-555-0148
        </li>
        <li>
          <svg viewBox="0 0 20 20"><circle cx="10" cy="10" r="8.5" fill="none" stroke="var(--royal)" stroke-width="1.6"/><rect x="7" y="5" width="6" height="10" rx="1" fill="none" stroke="var(--royal)" stroke-width="1.4"/></svg>
          772-555-0163
        </li>
        <li>
          <svg viewBox="0 0 20 20"><circle cx="10" cy="10" r="8.5" fill="none" stroke="var(--royal)" stroke-width="1.6"/><rect x="5.5" y="7" width="9" height="6.5" fill="var(--royal)"/><path d="M5.5 7l4.5 3.5L14.5 7" fill="none" stroke="#fff" stroke-width="1"/></svg>
          info@skyvornq.com
        </li>
        <li>
          <svg viewBox="0 0 20 20"><circle cx="10" cy="10" r="8" fill="none" stroke="var(--royal)" stroke-width="1.4"/><ellipse cx="10" cy="10" rx="3.5" ry="8" fill="none" stroke="var(--royal)" stroke-width="1.2"/><path d="M2 10h16M3.5 6h13M3.5 14h13" stroke="var(--royal)" stroke-width="1.1"/></svg>
          www.skyvornq.com
        </li>
        <li class="address">
          <svg viewBox="0 0 20 20"><circle cx="10" cy="10" r="8.5" fill="none" stroke="var(--royal)" stroke-width="1.6"/><path d="M10 15s-3.5-3.6-3.5-6a3.5 3.5 0 0 1 7 0c0 2.4-3.5 6-3.5 6z" fill="var(--royal)"/><circle cx="10" cy="9" r="1.3" fill="#fff"/></svg>
          <span>4827 Trellis Hollow Road,<br>Fort Pierce, Florida, 34951</span>
        </li>
      </ul>
    </div>
    <svg class="waves" viewBox="0 0 789 92" preserveAspectRatio="none" role="img" aria-label="Decorative navy and sky-blue wave band along the bottom edge">
      <defs>
        <linearGradient id="bandTone" x1="0" x2="1" y1="0" y2="0">
          <stop offset="0" stop-color="#14284f"/>
          <stop offset="0.6" stop-color="#1f5fa8"/>
          <stop offset="1" stop-color="#14284f"/>
        </linearGradient>
      </defs>
      <path d="M0 30 C200 10 420 40 600 38 C690 37 750 22 789 4 L789 92 L0 92 Z" fill="url(#bandTone)"/>
    </svg>
  </section>

  <section class="card card--back">
    <div class="brand">
      <span class="brand__ring"></span>
      <span class="brand__name">SKYVORNQ</span>
    </div>
    <p class="back__web">www.skyvornq.com</p>
  </section>

</div>
</body>
</html>
```